Coastline Premier Retreats Business Card Design

Design a business card for Coastline Premier Retreats. Look at the website for colors and reference. Card should have logo, name, title, office number, mobile number, email, URL and a tagline like, "Luxury Hotel & Resort Email Marketing" (This might change).

https://www.coastlinepremierretreats.example

The rest I will leave up to your imagination.

Contact Information for Business Card

Logo, name, title, office number, mobile number, email, URL and a tagline like, "Luxury Hotel & Resort Email Marketing" (This might change).

```html
<!DOCTYPE html>
<html lang="en">
<head>
<meta charset="UTF-8">
<title>Coastline Premier Retreats – Business Card</title>
<link href="https://fonts.googleapis.com/css2?family=Montserrat:wght@600;700;800&family=Open+Sans:wght@400;600&display=swap" rel="stylesheet">
<style>
  :root {
    --stage: #3b3b3b;
    --card: #1b1b1b;
    --orange: #f47a20;
    --white: #f2f2f2;
    --grey: #c8c8c8;
    --silver: #8e8e8e;
    --ink: #1b1b1b;
  }
  html, body {
    margin: 0;
    width: 1200px;
    height: 801px;
    overflow: hidden;
    background: var(--stage);
  }
  .stage {
    position: relative;
    width: 1200px;
    height: 801px;
  }
  .card {
    position: absolute;
    top: 258px;
    width: 520px;
    height: 297px;
    background: var(--card);
    border: 2px solid var(--orange);
    box-sizing: border-box;
    box-shadow: 0 18px 40px rgba(0,0,0,.45);
    overflow: hidden;
  }
  .card--front { left: 48px; }
  .card--back { left: 632px; }

  .brand {
    position: absolute;
    left: 30px;
    top: 92px;
    width: 205px;
    display: flex;
    align-items: center;
    gap: 10px;
  }
  .brand__mark {
    flex: none;
    width: 16px;
    height: 16px;
    background: var(--orange);
  }
  .brand__name {
    font-family: "Montserrat", sans-serif;
    font-weight: 800;
    font-size: 19px;
    line-height: 1.15;
    text-transform: uppercase;
    letter-spacing: .5px;
    color: var(--white);
  }
  .divider {
    position: absolute;
    left: 255px;
    top: 44px;
    width: 1px;
    height: 122px;
    background: var(--orange);
  }
  .contact {
    position: absolute;
    left: 275px;
    top: 42px;
    font-family: "Open Sans", sans-serif;
    color: var(--grey);
  }
  .contact__name {
    font-family: "Montserrat", sans-serif;
    font-weight: 700;
    font-size: 17px;
    color: var(--orange);
    text-transform: uppercase;
    margin: 0;
  }
  .contact__title {
    font-size: 12px;
    margin: 2px 0 12px;
  }
  .contact__list {
    list-style: none;
    padding: 0;
    margin: 0;
    font-size: 11.5px;
    line-height: 20px;
  }
  .contact__list li {
    display: flex;
    align-items: center;
    gap: 7px;
  }
  .contact__list svg {
    width: 11px;
    height: 11px;
    fill: var(--orange);
    flex: none;
  }
  .tagline {
    position: absolute;
    left: 0;
    right: 0;
    bottom: 28px;
    height: 40px;
    background: var(--orange);
    display: flex;
    align-items: center;
    justify-content: center;
    font-family: "Montserrat", sans-serif;
    font-weight: 800;
    font-size: 14px;
    letter-spacing: 2.4px;
    text-transform: uppercase;
    color: var(--ink);
  }
  .brand--back {
    left: 0;
    right: 0;
    top: 0;
    bottom: 0;
    width: auto;
    justify-content: center;
  }
  .brand--back .brand__mark { background: var(--silver); width: 20px; height: 20px; }
  .brand--back .brand__name { color: var(--silver); font-size: 26px; }
</style>
</head>
<body>
<main class="stage">
  <section class="card card--front" aria-label="Business card front">
    <div class="brand">
      <span class="brand__mark"></span>
      <span class="brand__name">Coastline Premier Retreats</span>
    </div>
    <div class="divider"></div>
    <div class="contact">
      <h1 class="contact__name">Darren Holloway</h1>
      <p class="contact__title">President / CEO</p>
      <ul class="contact__list">
        <li><svg viewBox="0 0 24 24"><path d="M6.6 10.8a15 15 0 0 0 6.6 6.6l2.2-2.2a1 1 0 0 1 1-.25 11.4 11.4 0 0 0 3.6.57 1 1 0 0 1 1 1V20a1 1 0 0 1-1 1A17 17 0 0 1 3 4a1 1 0 0 1 1-1h3.5a1 1 0 0 1 1 1c0 1.25.2 2.45.57 3.6a1 1 0 0 1-.25 1z"/></svg>555.204.7310</li>
        <li><svg viewBox="0 0 24 24"><path d="M2 5h20v2l-10 6L2 7zm0 4l10 6 10-6v10H2z"/></svg>info@coastlinepremierretreats.example</li>
        <li><svg viewBox="0 0 24 24"><circle cx="12" cy="12" r="10"/></svg>www.coastlinepremierretreats.example</li>
      </ul>
    </div>
    <div class="tagline">Luxury Hotel &amp; Resort Email Marketing</div>
  </section>

  <section class="card card--back" aria-label="Business card back">
    <div class="brand brand--back">
      <span class="brand__mark"></span>
      <span class="brand__name">Coastline Premier Retreats</span>
    </div>
  </section>
</main>
</body>
</html>
```